Bramble firearms training and consulting

Business card for a new firearms training company. I train persons on firearms safety, personal protection, shooting tactics and CHL.Im a Prior State trooper. I also served 4 years in IRaq as a Protection contractor with the Dept of State. Real world training for Real world situations. I would like the company name to be, BRAMBLE FIREARMS TRAINING AND CONSULTING. Im native american also. Ive provided pics. Put the name Bramble above the arrowhead but rotate the arrowhead to the right with it pointing right. Then place bramble inside the arrowhead. lets see both.
Industry/Entity Type
Business
Contact Information for Business Card
Christian Chatellier817-240-0488shadowtraining33@gmail.com

```html
<!DOCTYPE html>
<html lang="en">
<head>
<meta charset="utf-8">
<title>Bramble Firearms Training and Consulting — Business Card</title>
<link rel="stylesheet" href="https://fonts.googleapis.com/css2?family=Alegreya:wght@400&family=Arimo:wght@400;700&family=Kurale&display=swap">
<style>
  :root {
    --backdrop: #1c1c1c;
    --card: #f7f7f5;
    --brand-red: #7a1508;
    --ink: #141414;
    --rule: #222222;
  }
  * { box-sizing: border-box; margin: 0; padding: 0; }
  html, body {
    width: 1200px;
    height: 1000px;
    overflow: hidden;
    background: var(--backdrop);
  }
  .card {
    position: absolute;
    left: 100px;
    top: 194px;
    width: 1000px;
    height: 613px;
    background: var(--card);
  }
  .band {
    position: absolute;
    top: 158px;
    height: 294px;
    background: var(--brand-red);
  }
  .band--left-thick { left: 0; width: 45px; }
  .band--left-thin { left: 51px; width: 7px; }
  .band--right-thin { right: 51px; width: 7px; }
  .band--right-thick { right: 0; width: 45px; }

  .brand-name {
    position: absolute;
    left: 0;
    right: 0;
    top: 100px;
    text-align: center;
    font-family: "Arimo", sans-serif;
    font-weight: 700;
    font-size: 104px;
    line-height: 1;
    letter-spacing: 2px;
    color: var(--brand-red);
  }
  .tagline {
    position: absolute;
    left: 193px;
    width: 645px;
    top: 268px;
    text-align: center;
    font-family: "Arimo", sans-serif;
    font-size: 25px;
    color: var(--brand-red);
    letter-spacing: 0.3px;
  }
  .tagline-rule {
    position: absolute;
    left: 193px;
    width: 645px;
    top: 313px;
    height: 2px;
    background: var(--rule);
  }
  .person-name {
    position: absolute;
    left: 0;
    right: 0;
    top: 352px;
    text-align: center;
    font-family: "Alegreya", serif;
    font-size: 44px;
    color: var(--ink);
  }
  .person-title {
    position: absolute;
    left: 0;
    right: 0;
    top: 404px;
    text-align: center;
    font-family: "Kurale", serif;
    font-size: 18px;
    color: var(--ink);
  }
  .contact-list {
    position: absolute;
    left: 0;
    right: 0;
    top: 463px;
    list-style: none;
    display: flex;
    flex-direction: column;
    align-items: center;
    gap: 5px;
    font-family: "Kurale", serif;
    font-size: 20px;
    color: var(--ink);
  }
  .contact-item {
    display: flex;
    align-items: center;
    gap: 12px;
    line-height: 24px;
  }
  .contact-icon { width: 20px; height: 20px; flex: none; }
</style>
</head>
<body>
  <main class="card">
    <div class="band band--left-thick"></div>
    <div class="band band--left-thin"></div>
    <div class="band band--right-thin"></div>
    <div class="band band--right-thick"></div>

    <div class="brand-name">BRAMBLE</div>
    <div class="tagline">BRAMBLE FIREARMS TRAINING AND CONSULTING</div>
    <div class="tagline-rule"></div>

    <h1 class="person-name">Dorian Pellwick</h1>
    <p class="person-title">Trainer and Consultant</p>

    <ul class="contact-list">
      <li class="contact-item">
        <svg class="contact-icon" viewBox="0 0 20 20" aria-hidden="true">
          <circle cx="10" cy="10" r="8.5" fill="none" stroke="#141414" stroke-width="1.6"/>
          <path d="M7 5.5 L8.6 5.5 L9.2 7.8 L8.1 8.7 Q9 10.9 11.3 11.9 L12.2 10.8 L14.5 11.4 L14.5 13 Q13.8 14.5 12 14.2 Q6.4 12.8 5.8 7 Q5.8 5.7 7 5.5 Z" fill="#141414"/>
        </svg>
        <span>555-317-9062</span>
      </li>
      <li class="contact-item">
        <svg class="contact-icon" viewBox="0 0 20 20" aria-hidden="true">
          <circle cx="10" cy="10" r="9" fill="#141414"/>
          <rect x="5" y="6.5" width="10" height="7" fill="#f7f7f5"/>
          <path d="M5 6.5 L10 10.5 L15 6.5" fill="none" stroke="#141414" stroke-width="1.2"/>
        </svg>
        <span>bramblecourse58@mailvento.com</span>
      </li>
      <li class="contact-item">
        <svg class="contact-icon" viewBox="0 0 20 20" aria-hidden="true">
          <circle cx="10" cy="10" r="9" fill="#141414"/>
          <path d="M5 10 L10 5.5 L15 10 L13.5 10 L13.5 14.5 L11.2 14.5 L11.2 11.5 L8.8 11.5 L8.8 14.5 L6.5 14.5 L6.5 10 Z" fill="#f7f7f5"/>
        </svg>
        <span>48 Linden Row Ashford, NY 12045</span>
      </li>
    </ul>
  </main>
</body>
</html>
```